Need Business Card for our Real Estate Business with Sales Executive's Picture

PANTONE 484 C ( RED)

PANTONE 2766 C ( BLUE

Industry/Entity Type

Real Estate

Contact Information for Business Card

Name, Mobile, email, & picture of Person
Agency Phone, address, Web address

Requirements
Must have
• Our Logo Colours, Agent Picture,

```html
<!DOCTYPE html>
<html lang="en">
<head>
<meta charset="utf-8">
<title>Meridian Realty – Business Card</title>
<link href="https://fonts.googleapis.com/css2?family=Roboto+Condensed:wght@400;700&display=swap" rel="stylesheet">
<style>
  :root {
    --navy: #141b4d;
    --navy-light: #242f6e;
    --brand-red: #9a3324;
    --paper: #ffffff;
    --ink: #1d2233;
    --ink-soft: #4a5064;
    --backdrop: #e6e7ea;
  }
  * { box-sizing: border-box; margin: 0; padding: 0; }
  html, body { width: 1200px; height: 896px; overflow: hidden; }
  body {
    background: var(--backdrop);
    font-family: "Roboto Condensed", Arial, sans-serif;
    display: flex; flex-direction: column; align-items: center; justify-content: center;
    gap: 48px;
  }
  .card {
    width: 560px; height: 320px; border-radius: 22px; position: relative; overflow: hidden;
    box-shadow: 0 10px 30px rgba(20, 27, 77, 0.18);
  }

  /* Back side */
  .card-back {
    background: linear-gradient(135deg, var(--navy-light) 0%, var(--navy) 60%);
    display: flex; align-items: center; justify-content: center;
  }
  .brand { display: flex; align-items: center; gap: 12px; white-space: nowrap; }
  .brand-mark { width: 14px; height: 14px; flex: none; }
  .brand-name { font-weight: 400; letter-spacing: 0.14em; text-transform: uppercase; line-height: 1; }
  .card-back .brand-mark { background: var(--paper); }
  .card-back .brand-name { color: var(--paper); font-size: 44px; }

  /* Front side */
  .card-front { background: var(--paper); }
  .card-front .brand { position: absolute; left: 34px; top: 32px; gap: 10px; }
  .card-front .brand-mark { background: var(--brand-red); width: 10px; height: 10px; }
  .card-front .brand-name { color: var(--navy); font-size: 28px; }
  .agent { position: absolute; left: 34px; top: 92px; }
  .agent-name { font-weight: 700; font-size: 22px; color: var(--ink); letter-spacing: 0.03em; }
  .agent-role { font-size: 14px; color: var(--ink-soft); margin-top: 2px; }
  .contacts { position: absolute; left: 34px; top: 150px; list-style: none; }
  .contacts li {
    display: flex; align-items: center; gap: 8px;
    font-size: 14px; color: var(--ink-soft); line-height: 22px;
  }
  .contacts svg { width: 12px; height: 12px; fill: var(--navy); flex: none; }
  .agent-photo {
    position: absolute; right: 0; bottom: 46px; width: 230px; height: 190px;
    background: linear-gradient(180deg, #ffffff 0%, #e9ecf4 35%, #3b56a5 75%, #243a86 100%);
  }
  .divider { position: absolute; left: 0; right: 0; bottom: 44px; height: 2px; background: var(--brand-red); }
  .address-band {
    position: absolute; left: 0; right: 0; bottom: 0; height: 44px; background: var(--navy);
    color: var(--paper); font-size: 14px; letter-spacing: 0.02em;
    display: flex; align-items: center; justify-content: center;
  }
</style>
</head>
<body>

  <section class="card card-back" aria-label="Card back">
    <div class="brand">
      <span class="brand-mark"></span>
      <span class="brand-name">Meridian Realty</span>
    </div>
  </section>

  <section class="card card-front" aria-label="Card front">
    <div class="brand">
      <span class="brand-mark"></span>
      <span class="brand-name">Meridian Realty</span>
    </div>

    <div class="agent">
      <p class="agent-name">DANIEL REYES</p>
      <p class="agent-role">Managing Director</p>
    </div>

    <ul class="contacts">
      <li><svg viewBox="0 0 24 24"><path d="M6.6 10.8a15 15 0 0 0 6.6 6.6l2.2-2.2a1 1 0 0 1 1-.25 11.4 11.4 0 0 0 3.6.57 1 1 0 0 1 1 1V20a1 1 0 0 1-1 1A17 17 0 0 1 3 4a1 1 0 0 1 1-1h3.5a1 1 0 0 1 1 1c0 1.25.2 2.45.57 3.57a1 1 0 0 1-.25 1z"/></svg>+852 2140 5518</li>
      <li><svg viewBox="0 0 24 24"><path d="M6 3h12v5H6zM4 9h16a2 2 0 0 1 2 2v6h-4v4H6v-4H2v-6a2 2 0 0 1 2-2zm4 7v3h8v-3z"/></svg>+852 2140 5590</li>
      <li><svg viewBox="0 0 24 24"><path d="M3 5h18v14H3zm2 2v.5l7 4.5 7-4.5V7zm0 2.8V17h14V9.8l-7 4.5z"/></svg>info@meridianrealty.com</li>
      <li><svg viewBox="0 0 24 24"><path d="M12 2a10 10 0 1 0 0 20 10 10 0 0 0 0-20zm6.9 9h-3a15 15 0 0 0-1.3-5.6A8 8 0 0 1 18.9 11zM12 4.1A13 13 0 0 1 13.9 11h-3.8A13 13 0 0 1 12 4.1zM9.4 5.4A15 15 0 0 0 8.1 11h-3a8 8 0 0 1 4.3-5.6zM5.1 13h3a15 15 0 0 0 1.3 5.6A8 8 0 0 1 5.1 13zM12 19.9A13 13 0 0 1 10.1 13h3.8A13 13 0 0 1 12 19.9zm2.6-1.3a15 15 0 0 0 1.3-5.6h3a8 8 0 0 1-4.3 5.6z"/></svg>www.meridianrealty.com</li>
    </ul>

    <div class="agent-photo" role="img" aria-label="Portrait photo of the agent in a blue suit and striped tie"></div>
    <div class="divider"></div>
    <p class="address-band">Via dei Tigli, 48. 10121 Torino (TO)</p>
  </section>

</body>
</html>
```